I am looking to create a newly designed website for our national leadership conference which is entitled, "The Harbor of Momentum Leadership Summit". The Harbor of Momentum Leadership Summit is a national conference for student leaders that prepares them for career leadership success. The current website can be seen at www.harborofmomentumleadershipsummit.com.

My goal for the new site is to create a more updated, fresh, hip, and exciting look that appeals to the younger generation while also maintaining are professional appeal. The color should be black, white, and gold. We want there to be live videos played and places to insert pictures for the panels as well.

I look forward to seeing you the new creations.

Requirements
Must have
• Ability to play videos on the home page and throughout the website. Also, make sure that the website shows up clearly on an zTablet.
Nice to have
• Nice look

```html
<!DOCTYPE html>
<html lang="en">
<head>
<meta charset="utf-8">
<title>Harbor of Momentum — Speaker Profile</title>
<link href="https://fonts.googleapis.com/css2?family=Roboto:wght@300;400;500;700&display=swap" rel="stylesheet">
<style>
:root{
  --gold:#b98f3e;
  --gold-band:#bb9140;
  --gold-btn:#c39b52;
  --ink:#222222;
  --text:#444444;
  --partner:#555555;
  --grey-band:#f4f4f4;
  --dark:#262626;
  --white:#ffffff;
}
*{box-sizing:border-box;margin:0;padding:0}
html,body{width:821px;height:1200px;overflow:hidden}
body{position:relative;background:var(--white);font-family:'Roboto',Arial,sans-serif;color:var(--text)}
.abs{position:absolute}

/* header */
.follow{left:51px;top:36px;font-size:8px;font-weight:500;color:var(--ink);display:flex;align-items:center;gap:5px}
.follow .sq{width:20px;height:20px;background:#555;display:inline-block}
.brand{left:0;width:821px;top:18px;text-align:center}
.brand .dot{display:block;margin:0 auto 4px;width:36px;height:36px;border-radius:50%;background:linear-gradient(135deg,#e0c27a,#a57b2c)}
.brand .name{font-size:11px;font-weight:700;letter-spacing:1px;color:var(--ink);white-space:nowrap}
.register-btn{left:618px;top:24px;width:152px;height:35px;border-radius:18px;background:var(--gold-btn);color:var(--white);font-size:15px;font-weight:500;letter-spacing:.5px;display:flex;align-items:center;justify-content:center}

/* nav */
.nav{left:0;top:85px;width:821px;height:42px;background:linear-gradient(#333,#151515);display:flex;padding-left:58px}
.nav a{color:var(--white);font-size:10px;font-weight:500;text-decoration:none;display:flex;align-items:center;padding:0 16px;height:42px;white-space:nowrap}
.nav a.active{background:var(--gold-btn);padding:0 12px}
.nav a.wide{padding:0 24px}

.crumb{left:56px;top:150px;font-size:8px;color:#555}
.crumb b{color:var(--gold);font-weight:500}

/* logo bands */
.band{left:0;width:821px;background:var(--grey-band)}
.band-logo{width:34px;height:34px;border-radius:50%;background:linear-gradient(135deg,#e0c27a,#a57b2c)}
.band-title{font-size:16px;font-weight:400;color:var(--ink);line-height:19px;letter-spacing:.5px;white-space:nowrap}
.band-title span{color:var(--gold)}
.arrow{width:10px;height:16px}
.logos{display:flex;align-items:center;justify-content:space-around}
.partner{font-size:15px;font-weight:700;color:var(--partner);white-space:nowrap}

/* section title */
.sec-title{left:0;width:821px;display:flex;justify-content:center;align-items:center;gap:14px;font-size:16px;font-weight:400;color:var(--ink);letter-spacing:.5px}
.sec-title .accent{color:var(--gold)}
.sec-title i{width:32px;height:32px;border-radius:50%;background:linear-gradient(135deg,#e0c27a,#a57b2c);display:inline-block}

.intro{left:51px;top:343px;width:398px;font-size:9.4px;line-height:16.5px;font-weight:300;color:#333}
.intro p{margin-bottom:6px}
.photo{left:477px;top:346px;width:293px;height:195px;background:linear-gradient(120deg,#5d6a6c,#8d8a86 45%,#c5c0b8 70%,#6f6a63)}

/* gold band */
.roles{left:0;top:571px;width:821px;height:282px;background:var(--gold-band);display:flex;justify-content:center;padding-left:18px}
.role{width:184px;text-align:center;padding-top:28px}
.role .circ{width:77px;height:77px;border-radius:50%;background:var(--white);margin:0 auto;display:flex;align-items:center;justify-content:center}
.role h3{color:var(--white);font-size:13px;font-weight:500;margin-top:16px;letter-spacing:.2px;white-space:nowrap}
.role p{color:#f1e4c7;font-size:9.2px;font-weight:300;line-height:16px;margin-top:10px;padding:0 6px}
.role .more{display:inline-block;margin-top:21px;width:88px;height:26px;line-height:26px;border-radius:13px;background:#1e1e1e;color:var(--white);font-size:9.5px;font-weight:500}

/* countdown */
.count{top:1015px;left:0;width:821px;display:flex;justify-content:center;gap:25px}
.count .box{width:50px;height:54px;background:#1a1a1a;border:2px solid #555;border-radius:3px;text-align:center;color:var(--white)}
.count .num{font-size:22px;color:#d4a956;font-weight:500;line-height:30px;margin-top:4px}
.count .lbl{font-size:7px;font-weight:500}

/* footer */
.footer{left:0;top:1084px;width:821px;height:116px;background:var(--dark)}
.fnav{left:51px;top:38px;display:flex;gap:20px}
.fnav a{color:var(--white);font-size:8px;font-weight:500;text-decoration:none}
.copy{left:51px;top:72px;font-size:8px;line-height:14px;color:#bbb}
.fbrand{left:620px;top:30px;width:180px;text-align:center}
.fbrand i{display:block;margin:0 auto 8px;width:38px;height:38px;border-radius:50%;background:#6e6e6e}
.fbrand span{font-size:11px;font-weight:700;letter-spacing:1px;color:#7d7d7d;white-space:nowrap}
</style>
</head>
<body>

<header>
  <div class="abs follow">FOLLOW US <span class="sq"></span><span class="sq"></span><span class="sq"></span><span class="sq"></span><span class="sq"></span></div>
  <div class="abs brand"><i class="dot"></i><span class="name">HARBOR OF MOMENTUM</span></div>
  <a class="abs register-btn">REGISTER NOW</a>
</header>

<nav class="abs nav">
  <a>HOME</a><a>ABOUT</a><a>CONFERENCE PROGRAMS</a><a>REGISTER</a><a class="active">SPEAKER PROFILES</a><a class="wide">REGIONAL CONFERENCES</a><a class="wide">CONTACT</a>
</nav>

<div class="abs crumb">HOME &nbsp;»&nbsp; <b>SPEAKER PROFILE</b></div>

<section class="abs band" style="top:172px;height:90px">
  <div class="abs band-logo" style="left:52px;top:30px"></div>
  <div class="abs band-title" style="left:104px;top:27px">NETWORK WITH<br><span>EXECUTIVES</span></div>
  <svg class="abs arrow" style="left:261px;top:37px" viewBox="0 0 10 16"><path d="M8 1 2 8l6 7" fill="none" stroke="#222" stroke-width="2"/></svg>
  <div class="abs logos" style="left:282px;top:18px;width:470px;height:52px">
    <span class="partner">Crestline</span>
    <span class="partner">Marlow</span>
    <span class="partner">Vivid Sound</span>
    <span class="partner">Norvek</span>
    <span class="partner">Jolly's</span>
  </div>
  <svg class="abs arrow" style="left:761px;top:37px" viewBox="0 0 10 16"><path d="M2 1l6 7-6 7" fill="none" stroke="#222" stroke-width="2"/></svg>
</section>

<h2 class="abs sec-title" style="top:290px"><i></i><span>SPEAKER <span class="accent">PROFILE</span></span></h2>

<div class="abs intro">
  <p>The Harbor of Momentum Leadership Summit not only provides student leaders with an incredible leadership experience, but our leadership team brings together some of the top keynote speakers, workshop presenters, and panelist in the country. Each year, students are transformed by the amazing knowledge, insight, wisdom, and inspiration that is shared by our amazing team of speakers</p>
  <p>Take some time to learn more about these dynamic keynote speakers, workshop presenters, and panelist that impact the lives of student leaders every year at the Harbor of Momentum Leadership Experience.</p>
</div>
<div class="abs photo" role="img" aria-label="Photo of two speakers seated together at the summit"></div>

<section class="abs roles">
  <div class="role">
    <div class="circ"><svg width="28" height="28" viewBox="0 0 28 28" fill="#1e1e1e"><circle cx="14" cy="6" r="3"/><rect x="11" y="10" width="6" height="10"/><rect x="9" y="22" width="10" height="4"/><circle cx="4" cy="11" r="2"/><rect x="2" y="14" width="4" height="8"/><circle cx="24" cy="11" r="2"/><rect x="22" y="14" width="4" height="8"/></svg></div>
    <h3>Keynote Speaker</h3>
    <p>Students will learn about more than twenty different leadership skills and qualities that leaders must possess in the 21st Century in order</p>
    <span class="more">Read More</span>
  </div>
  <div class="role">
    <div class="circ"><svg width="28" height="28" viewBox="0 0 28 28" fill="#1e1e1e"><rect x="10" y="3" width="16" height="11" fill="none" stroke="#1e1e1e" stroke-width="1.6"/><path d="M13 11l4-4 3 3 4-4" fill="none" stroke="#1e1e1e" stroke-width="1.4"/><circle cx="5" cy="8" r="2.5"/><rect x="3" y="11" width="4" height="5"/><circle cx="6" cy="19" r="2"/><circle cx="12" cy="19" r="2"/><circle cx="18" cy="19" r="2"/><circle cx="24" cy="19" r="2"/><rect x="3" y="22" width="24" height="4"/></svg></div>
    <h3>Workshop Presenters</h3>
    <p>Students will learn about more than twenty different leadership skills and qualities that leaders must possess in the 21st Century in order</p>
    <span class="more">Read More</span>
  </div>
  <div class="role">
    <div class="circ"><svg width="28" height="28" viewBox="0 0 28 28" fill="#1e1e1e"><circle cx="9" cy="5" r="2.5"/><circle cx="19" cy="5" r="2.5"/><circle cx="3" cy="11" r="2.5"/><circle cx="25" cy="11" r="2.5"/><rect x="7" y="9" width="14" height="8"/><rect x="1" y="15" width="4" height="9"/><rect x="23" y="15" width="4" height="9"/><rect x="12" y="17" width="4" height="9"/></svg></div>
    <h3>Career Panelist Experts</h3>
    <p>Students will learn about more than twenty different leadership skills and qualities that leaders must possess in the 21st Century in order</p>
    <span class="more">Read More</span>
  </div>
  <div class="role">
    <div class="circ"><svg width="28" height="28" viewBox="0 0 28 28" fill="#1e1e1e"><circle cx="6" cy="6" r="3"/><circle cx="14" cy="5" r="3"/><circle cx="22" cy="6" r="3"/><rect x="3" y="10" width="6" height="8"/><rect x="11" y="9" width="6" height="9"/><rect x="19" y="10" width="6" height="8"/><rect x="4" y="18" width="4" height="7"/><rect x="12" y="18" width="4" height="8"/><rect x="20" y="18" width="4" height="7"/></svg></div>
    <h3>Leadership Executives</h3>
    <p>Students will learn about more than twenty different leadership skills and qualities that leaders must possess in the 21st Century in order</p>
    <span class="more">Read More</span>
  </div>
</section>

<section class="abs band" style="top:853px;height:92px">
  <div class="abs band-logo" style="left:52px;top:33px"></div>
  <div class="abs band-title" style="left:104px;top:18px">2015 CONFERENCE<br><span>PARTNERS AND<br>SUPPORTS</span></div>
  <svg class="abs arrow" style="left:261px;top:38px" viewBox="0 0 10 16"><path d="M8 1 2 8l6 7" fill="none" stroke="#222" stroke-width="2"/></svg>
  <div class="abs logos" style="left:280px;top:14px;width:472px;height:64px">
    <span class="partner">Westfield Power</span>
    <span class="partner">Kaito</span>
    <span class="partner">Bramble</span>
    <span class="partner">Salsa Verde</span>
    <span class="partner">Honor Guild</span>
  </div>
  <svg class="abs arrow" style="left:761px;top:38px" viewBox="0 0 10 16"><path d="M2 1l6 7-6 7" fill="none" stroke="#222" stroke-width="2"/></svg>
</section>

<h2 class="abs sec-title" style="top:965px"><i></i><span>6TH ANNUAL <span class="accent">CONFERENCE COUNTDOWN</span></span></h2>

<div class="abs count">
  <div class="box"><div class="num">0</div><div class="lbl">HOURS</div></div>
  <div class="box"><div class="num">0</div><div class="lbl">MINUTES</div></div>
  <div class="box"><div class="num">0</div><div class="lbl">SECONDS</div></div>
</div>

<footer class="abs footer">
  <nav class="abs fnav"><a>HOME</a><a>ABOUT</a><a>CONFERENCE</a><a>REGISTER</a><a>TESTIMONIALS</a><a>Y FACTOR</a><a>VIDEOS</a><a>CONTACT</a></nav>
  <div class="abs copy">Copyright © 2015. Company Name All Right Reserved<br>Privacy Policy &nbsp;|&nbsp; Term &amp; Conditions</div>
  <div class="abs fbrand"><i></i><span>HARBOR OF MOMENTUM</span></div>
</footer>

</body>
</html>
```